Web Site Mock Up's for a Dog Food Business

We are a supplier of bespoke dog food. We tailor our dog food to meet the dogs needs.We are looking for ideas (mock ups) of design ideas for our new web site - Just mock ups - web site will follow if we are happy with the mock ups.I have included our logo (PSD file). I have also included a rough (please don’t copy) home page with the information we would ideally like on the page. Note the page will have sliders at the top, we have done two example sliders, and included a video to be included.I have also enclosed the questions we need to find out in order to develop a dogs food.I would like to see a home page, and a tell us about your dog page.Would like mock ups as PSD files, so we can play around with.I am open to ideas and better designs. DO NOT JUST COPY MY LAYOUTSome of our competitors sites include www.tails.comwww.paws.comwww.parcelpet.comwww.growlingtums.co.ukI want a clean, bright easy to navigate site. Happy to play around with colours - doesn’t have to be the browns I have used. Happy to use both infographics and photo of real dogs, but I do want site to look like the best food available for dogs.Web site will be a database driven site, with around 10 -15 pages plus about 60 dynamic database driven pages of products (all same layout )Look forward to receiving your ideas.

```html
<!DOCTYPE html>
<html lang="en">
<head>
<meta charset="utf-8">
<title>kibblora.co.uk – Home</title>
<link href="https://fonts.googleapis.com/css2?family=Poppins:wght@300;400;500;600;700&display=swap" rel="stylesheet">
<style>
:root{
  --brown:#5a3219;
  --brown-box:#5b3418;
  --purple-light:#5535a6;
  --purple-dark:#3f1f98;
  --blue:#3a8aab;
  --green:#5f9e35;
  --grey-text:#777;
  --numeral:#d4d4d4;
  --footer:#0d0d0d;
  --white:#fff;
  --line:#c9c9c9;
}
*{margin:0;padding:0;box-sizing:border-box}
html,body{width:1200px;height:3371px;overflow:hidden}
body{position:relative;font-family:'Poppins',sans-serif;background:var(--white);color:#333}
.abs{position:absolute}

/* header */
.site-header{left:0;top:0;width:1200px;height:108px;background:var(--white);z-index:3}
.logo-plate{left:130px;top:-60px;width:305px;height:230px;border-radius:50%;background:var(--white);z-index:4}
.logo-name{left:130px;top:78px;width:305px;text-align:center;font-weight:700;font-size:24px;color:var(--brown);z-index:5}
.logo-dot{display:inline-block;width:14px;height:14px;border-radius:50%;background:var(--brown);margin-right:8px;vertical-align:middle}
.main-nav{right:110px;top:40px;display:flex;gap:30px;font-size:15px;color:#444;z-index:5}

/* hero */
.hero{left:0;top:108px;width:1200px;height:602px;background:linear-gradient(180deg,#8a8a8a 0%,#6b6b6b 60%,#9c9c9c 100%)}
.hero-photo{left:0;top:0;width:1200px;height:602px;background:radial-gradient(ellipse at 52% 55%,#a58a5e 0%,#6f6558 35%,rgba(100,100,100,0) 70%)}
.play{left:550px;top:159px;width:100px;height:100px}
.hero-title{left:0;top:270px;width:1200px;text-align:center;color:var(--white);font-weight:600;font-size:34px;line-height:48px}
.hero-btn{left:452px;top:386px;width:296px;height:56px;border:3px solid var(--white);border-radius:30px;color:var(--white);font-weight:600;font-size:17px;display:flex;align-items:center;justify-content:center}
.slider-dots{left:1130px;top:250px;width:30px}
.slider-dots span{display:block;width:14px;height:14px;border-radius:50%;background:var(--white);margin:0 auto 13px}
.slider-dots span.active{width:26px;height:26px;background:none;border:3px solid var(--white);position:relative}
.slider-dots span.active::after{content:"";position:absolute;left:5px;top:5px;width:10px;height:10px;border-radius:50%;background:var(--white)}

/* section titles */
.section-title{left:0;width:1200px;text-align:center;font-weight:600;font-size:40px;color:var(--brown)}

/* how it works */
.step-circle{width:152px;height:152px;border-radius:50%;background:var(--brown);display:flex;align-items:center;justify-content:center}
.step-label{width:300px;text-align:center;font-size:23px;line-height:36px;color:#555}
.step-num{width:300px;text-align:center;font-size:46px;font-weight:600;color:var(--numeral)}
.bowl-art{left:0;top:1236px;width:250px;height:150px;background:radial-gradient(ellipse at 50% 60%,#eeeeee 0%,#f7f7f7 50%,rgba(255,255,255,0) 72%)}

/* foods */
.foods-intro{left:0;top:1450px;width:1200px;text-align:center;font-size:19px;line-height:30px;color:#555}
.card-peek-left{left:0;top:1553px;width:79px;height:517px;background:var(--blue);border-radius:0 14px 14px 0}
.card-peek-right{left:1121px;top:1553px;width:79px;height:517px;background:var(--green);border-radius:14px 0 0 14px}
.food-card{left:110px;top:1553px;width:980px;height:517px;border-radius:14px;overflow:hidden;background:var(--purple-dark)}
.food-card .half-light{left:0;top:0;width:512px;height:517px;background:var(--purple-light)}
.food-card .half-dark{left:512px;top:0;width:468px;height:517px;background:radial-gradient(circle at 45% 50%,#5a3bbf 0%,var(--purple-dark) 65%)}
.food-title{right:546px;top:135px;font-size:28px;font-weight:500;color:var(--white);text-align:right}
.food-desc{right:546px;top:186px;width:320px;font-size:16px;line-height:26px;color:var(--white);text-align:right;font-weight:500}
.food-btn{left:263px;top:303px;width:171px;height:47px;border:2px solid var(--white);border-radius:26px;color:var(--white);font-weight:600;font-size:16px;display:flex;align-items:center;justify-content:center}
.pack-art{left:627px;top:96px;width:240px;height:324px;background:linear-gradient(180deg,#f3f0ea 0%,#e9e2d4 45%,#e2a24a 70%,#f1ece2 100%);border:4px solid var(--white)}

/* testimonials */
.testimonial{top:2281px;width:306px;height:269px;border:2px solid #d9d9d9;border-radius:4px;background:var(--white);text-align:center}
.avatar{top:2241px;width:84px;height:84px;border-radius:50%;border:3px solid var(--white);box-shadow:0 0 0 1px #ddd}
.quote{position:absolute;left:28px;top:60px;width:250px;font-size:13.5px;line-height:25px;color:#888}
.who{position:absolute;left:0;top:190px;width:100%;font-size:16px;font-weight:500;color:var(--brown)}
.where{position:absolute;left:0;top:215px;width:100%;font-size:14px;color:#666}

/* contact */
.contact-box{left:542px;top:2744px;width:546px;height:458px;background:var(--brown-box)}
.footer{left:0;top:3090px;width:1200px;height:281px;background:var(--footer)}
.contact-dog{left:888px;top:3022px;width:200px;height:180px;background:radial-gradient(ellipse at 55% 55%,#8a5a30 0%,#6a4020 45%,rgba(91,52,24,0) 75%)}
.form-card{left:110px;top:2780px;width:501px;height:390px;background:var(--white);box-shadow:0 0 12px rgba(0,0,0,.15)}
.form-title{left:24px;top:24px;font-size:30px;font-weight:600;color:var(--brown)}
.field{height:41px;border:2px solid #d2d2d2;font-size:13px;color:#aaa;padding:10px 14px}
.submit{left:25px;top:319px;width:126px;height:40px;border-radius:22px;background:var(--brown);color:var(--white);font-weight:600;font-size:16px;display:flex;align-items:center;justify-content:center}
.contact-title{left:134px;top:88px;font-size:30px;font-weight:600;color:var(--white)}
.contact-item{left:134px;font-size:19px;line-height:30px;color:var(--white);display:flex;gap:20px;font-weight:500}
.contact-item svg{flex:none;margin-top:6px}

/* footer */
.social{top:3171px;width:28px;height:28px;border-radius:50%;background:var(--white)}
.footer-nav{left:0;top:3282px;width:1200px;text-align:center;font-size:15px;color:var(--white);word-spacing:4px}
.copyright{left:0;top:3321px;width:1200px;text-align:center;font-size:14px;color:var(--white)}
</style>
</head>
<body>

<header class="site-header abs"></header>
<div class="logo-plate abs"></div>
<div class="logo-name abs"><span class="logo-dot"></span>kibblora.co.uk</div>
<nav class="main-nav abs">
  <span>Home</span><span>Our Food</span><span>How it Works</span><span>Pricing</span><span>Customer Reviews</span><span>FAQs</span>
</nav>

<section class="hero abs">
  <div class="hero-photo abs" role="img" aria-label="Photo of a beagle eating from a steel food bowl"></div>
  <svg class="play abs" viewBox="0 0 100 100"><circle cx="50" cy="50" r="46" fill="#fff" fill-opacity=".9" stroke="#fff" stroke-width="4"/><circle cx="50" cy="50" r="38" fill="none" stroke="#333" stroke-width="3"/><path d="M40 32 L68 50 L40 68 Z" fill="#333"/></svg>
  <h1 class="hero-title abs">Food Unique As Your Dog Blended Using<br>The Finest Ingredients</h1>
  <div class="hero-btn abs">Tell Us About Your Dog</div>
  <div class="slider-dots abs"><span class="active"></span><span></span><span></span><span></span></div>
</section>

<h2 class="section-title abs" style="top:780px">How It Works</h2>
<svg class="abs" style="left:340px;top:900px" width="200" height="60" viewBox="0 0 200 60"><path d="M185 40 C140 -5 60 -5 18 50" fill="none" stroke="#555" stroke-width="2.5" stroke-dasharray="6 6"/><path d="M10 58 L14 42 L26 52 Z" fill="#555"/></svg>
<svg class="abs" style="left:668px;top:975px" width="200" height="60" viewBox="0 0 200 60"><path d="M5 20 C50 60 130 50 178 12" fill="none" stroke="#555" stroke-width="2.5" stroke-dasharray="6 6"/><path d="M190 4 L184 19 L173 8 Z" fill="#555"/></svg>

<div class="step-circle abs" style="left:187px;top:906px">
  <svg width="84" height="80" viewBox="0 0 84 80" fill="none" stroke="#fff" stroke-width="4" stroke-linecap="round"><path d="M22 18 C10 10 2 22 6 40 C10 42 16 36 18 28"/><path d="M62 18 C74 10 82 22 78 40 C74 42 68 36 66 28"/><path d="M20 26 C22 10 62 10 64 26 L66 50 C66 70 18 70 18 50 Z"/><circle cx="32" cy="38" r="2" fill="#fff"/><circle cx="52" cy="38" r="2" fill="#fff"/><path d="M36 50 h12 l-6 6 Z" fill="#fff"/></svg>
</div>
<div class="step-circle abs" style="left:524px;top:906px">
  <svg width="64" height="84" viewBox="0 0 64 84" fill="none" stroke="#fff" stroke-width="4"><rect x="8" y="6" width="48" height="72" rx="4"/><path d="M8 20 H56 M8 64 H56"/><circle cx="32" cy="46" r="6" fill="#fff"/><circle cx="22" cy="36" r="3" fill="#fff"/><circle cx="30" cy="31" r="3" fill="#fff"/><circle cx="38" cy="31" r="3" fill="#fff"/><circle cx="44" cy="37" r="3" fill="#fff"/></svg>
</div>
<div class="step-circle abs" style="left:879px;top:906px">
  <svg width="92" height="60" viewBox="0 0 92 60" fill="none" stroke="#fff" stroke-width="4"><rect x="4" y="8" width="52" height="36"/><path d="M56 20 H74 L86 34 V44 H56"/><circle cx="20" cy="48" r="6" fill="#5a3219"/><circle cx="70" cy="48" r="6" fill="#5a3219"/><circle cx="30" cy="28" r="4" fill="#fff"/></svg>
</div>
<div class="step-label abs" style="left:113px;top:1094px">Tell Us About<br>Your Dog</div>
<div class="step-label abs" style="left:450px;top:1094px">We Create<br>Your Food</div>
<div class="step-label abs" style="left:805px;top:1112px">We Delivery</div>
<div class="step-num abs" style="left:103px;top:1184px">01</div>
<div class="step-num abs" style="left:440px;top:1184px">02</div>
<div class="step-num abs" style="left:813px;top:1184px">03</div>
<div class="bowl-art abs" role="img" aria-label="White bowl filled with dry dog food"></div>

<h2 class="section-title abs" style="top:1378px">Our Foods</h2>
<p class="foods-intro abs">We develop and create your dogs ideal food using the finest ingredients,<br>based on your dogs requirements.</p>

<div class="card-peek-left abs"></div>
<div class="card-peek-right abs"></div>
<div class="food-card abs">
  <div class="half-light abs"></div>
  <div class="half-dark abs"></div>
  <h3 class="food-title abs">Puppy Food</h3>
  <p class="food-desc abs">A well balanced and nutritious range of foods to meet the needs of growing puppies of all breeds.</p>
  <div class="food-btn abs">Tell Me More</div>
  <div class="pack-art abs" role="img" aria-label="Illustrated puppy food bag"></div>
</div>

<h2 class="section-title abs" style="top:2151px">Testimonials</h2>
<div class="testimonial abs" style="left:110px">
  <p class="quote">I have 3 dogs all on different foods. No more trips to the shops fetching massive bags of food. This works for me and my dogs love it.</p>
  <div class="who">Nell with Barley</div><div class="where">– Ashcombe</div>
</div>
<div class="testimonial abs" style="left:447px">
  <p class="quote">My dog is a really fussy eater and has a very sensitive stomach. I found my ideal food here, which suits him. GREAT !!</p>
  <div class="who">Tom, Pip and Rolo</div><div class="where">– Brindlemoor</div>
</div>
<div class="testimonial abs" style="left:780px">
  <p class="quote">My dog is on the itchy skin formula, and although she still itches sometimes its much better. Its cheaper than the vets options, and a great service.</p>
  <div class="who">Mrs Hart with Tilly</div><div class="where">– Wenford</div>
</div>
<div class="avatar abs" style="left:221px;background:linear-gradient(160deg,#e3c48c,#c9a27a)" role="img" aria-label="Customer portrait photo"></div>
<div class="avatar abs" style="left:558px;background:linear-gradient(160deg,#c9c9c9,#b08a74)" role="img" aria-label="Customer portrait photo"></div>
<div class="avatar abs" style="left:891px;background:linear-gradient(160deg,#8fa5b0,#6d5a4f)" role="img" aria-label="Customer portrait photo"></div>

<h2 class="section-title abs" style="top:2640px">Contact Us</h2>
<div class="footer abs"></div>
<div class="contact-box abs">
  <h3 class="contact-title abs">Contact Us</h3>
  <div class="contact-item abs" style="top:160px"><svg width="18" height="24" viewBox="0 0 18 24"><path d="M9 1 C4 1 1 5 1 9 C1 15 9 23 9 23 C9 23 17 15 17 9 C17 5 14 1 9 1 Z" fill="#fff"/><circle cx="9" cy="9" r="3" fill="#5b3418"/></svg><span>#10, Lorem ipsum dolor sit amet,<br>consectetur adipiscing elit</span></div>
  <div class="contact-item abs" style="top:254px"><svg width="18" height="18" viewBox="0 0 24 24"><path d="M6 2 L10 7 L8 10 C9 13 11 15 14 16 L17 14 L22 18 L19 22 C10 21 3 14 2 5 Z" fill="#fff"/></svg><span>+1 5550198274</span></div>
  <div class="contact-item abs" style="top:317px"><svg width="18" height="14" viewBox="0 0 18 14"><rect x="0" y="0" width="18" height="14" fill="#fff"/><path d="M0 0 L9 8 L18 0" fill="none" stroke="#5b3418" stroke-width="1.5"/></svg><span>info@kibblora.com</span></div>
</div>
<div class="contact-dog abs" role="img" aria-label="Photo of a puppy beside a food bowl"></div>
<div class="form-card abs">
  <h3 class="form-title abs">Get In Touch</h3>
  <div class="field abs" style="left:27px;top:87px;width:207px">Name</div>
  <div class="field abs" style="left:254px;top:87px;width:209px">Email</div>
  <div class="field abs" style="left:27px;top:148px;width:207px">Phone Number</div>
  <div class="field abs" style="left:254px;top:148px;width:209px">Subject</div>
  <div class="field abs" style="left:27px;top:208px;width:436px;height:84px">Message</div>
  <div class="submit abs">Submit</div>
</div>

<div class="social abs" style="left:562px" role="img" aria-label="Social link"></div>
<div class="social abs" style="left:610px" role="img" aria-label="Social link"></div>
<nav class="footer-nav abs">Home Our Food How it Works Pricing Customer Reviews FAQs</nav>
<p class="copyright abs">© 2018 Copyrights | All Rights Reserved | Terms &amp; Conditions | Privacy Policy</p>

</body>
</html>
```